Garden Design Flier

I would like a PDF of this half page A4 flier in soft green tones with dark green leaves.

Target Market(s)

Home owners and real estate agents

Font styles to use
Serif
Other font styles liked:
• Papyrus

Colors
acd136
9bcb3c
cadf82
fefdec

Requirements
Must have
• Green tones
Nice to have
• Leaves, vines, lawns
Should not have
• Open to ideas, but classic style

```html
<!DOCTYPE html>
<html lang="en">
<head>
<meta charset="utf-8">
<title>Verdant Gardens – Flier</title>
<link rel="stylesheet" href="https://fonts.googleapis.com/css2?family=Macondo&family=Montserrat:wght@700&display=swap">
<style>
  :root {
    --leaf-deep: #4f5e24;
    --leaf-mid: #9bb86a;
    --leaf-soft: #cadf82;
    --leaf-pale: #e6efc8;
    --paper: #ffffff;
    --ink: #1f2312;
  }
  html, body {
    margin: 0;
    padding: 0;
    overflow: hidden;
    background: var(--paper);
  }
  .flier {
    position: relative;
    width: 1200px;
    height: 846px;
    overflow: hidden;
    font-family: "Macondo", fantasy;
  }
  .foliage-backdrop {
    position: absolute;
    inset: 0;
    background:
      radial-gradient(ellipse at 10% 20%, var(--leaf-soft) 0%, transparent 45%),
      radial-gradient(ellipse at 90% 30%, var(--leaf-mid) 0%, transparent 40%),
      radial-gradient(ellipse at 15% 85%, var(--leaf-mid) 0%, transparent 45%),
      radial-gradient(ellipse at 85% 90%, var(--leaf-soft) 0%, transparent 45%),
      var(--leaf-pale);
  }
  .panel {
    position: absolute;
    left: 104px;
    top: 77px;
    width: 972px;
    height: 675px;
    background: var(--paper);
    border: 10px solid var(--leaf-deep);
  }
  .line {
    position: absolute;
    left: 0;
    width: 1200px;
    margin: 0;
    text-align: center;
    white-space: nowrap;
  }
  .brand-name {
    top: 118px;
    font-size: 132px;
    line-height: 132px;
    color: var(--leaf-deep);
    letter-spacing: 2px;
  }
  .brand-sub {
    top: 247px;
    font-family: "Montserrat", sans-serif;
    font-weight: 700;
    font-size: 36px;
    line-height: 36px;
    letter-spacing: 27px;
    padding-left: 27px;
    color: var(--leaf-deep);
  }
  .byline {
    top: 314px;
    font-size: 33px;
    line-height: 36px;
    color: var(--ink);
  }
  .byline small { font-size: 22px; }
  .credential {
    top: 364px;
    font-size: 27px;
    line-height: 30px;
    color: var(--ink);
  }
  .services {
    top: 438px;
    font-size: 57px;
    line-height: 60px;
    color: var(--leaf-deep);
    word-spacing: 4px;
  }
  .services .dot { font-size: 40px; vertical-align: 6px; margin: 0 10px; }
  .pitch {
    top: 536px;
    font-size: 29px;
    line-height: 40px;
    color: var(--ink);
  }
  .rule {
    position: absolute;
    left: 161px;
    top: 694px;
    width: 878px;
    height: 1px;
    background: var(--leaf-deep);
  }
  .contact {
    position: absolute;
    left: 161px;
    top: 712px;
    width: 878px;
    display: flex;
    justify-content: space-between;
    font-size: 21px;
    line-height: 26px;
    color: var(--ink);
    white-space: nowrap;
  }
</style>
</head>
<body>
<main class="flier">
  <div class="foliage-backdrop" role="img" aria-label="Watercolour pattern of soft green leaves and vines"></div>
  <section class="panel"></section>

  <h1 class="line brand-name">VERDANT</h1>
  <p class="line brand-sub">GARDENS</p>
  <p class="line byline"><small>by</small> MILES HARTWELL</p>
  <p class="line credential">Certificate 3. Horticulture, Northfield Trade College</p>
  <p class="line services">Design<span class="dot">●</span>Install<span class="dot">●</span>Grow<span class="dot">●</span>Tend<span class="dot">●</span>Enjoy</p>
  <p class="line pitch">All your gardening and landscaping needs from design<br>and installation to general maintenance. Bespoke vegetable gardens<br>and potager designs created to suit your site and requirements</p>

  <div class="rule"></div>
  <footer class="contact">
    <span>email: miles@verdantgardens.example.au</span>
    <span>|</span>
    <span>Call : 0400-123456</span>
    <span>|</span>
    <span>ABN:12345678901</span>
  </footer>
</main>
</body>
</html>
```